Letterhead Design for Law Firm

**Edit: I have added the photo of a bottom that I like.

------
We are looking for a re-design of our new letterhead. The letterhead is for a law firm and will be used for digital and traditionally printed correspondence.

Here are some suggestions:

- Please use colours are #8ec900 and simple black.
- Please do not use any type of "waves" at the bottom of the page. This is not in style at all.
- Please stay modern yet conservative.
- Please use font Segoe UI Light or similar if you can
- Avoid clipart or illustrations.
- Utilize ample white space in the layout so the design looks clean and information is easy to read at a glance. Don't overcrowd the letterhead.
- Make sure the letterhead design is consistent with our brand identity (see corvelith.ca)
-Please, no black headers or footers.

I am attaching my current letterhead and signature for your convenience.

Remember, the letterhead is an extension of our professional identity. We are a successful firm and trial lawyers who correspond with insurers, judges, lawyers, courts, clients, etc. Make it new, modern, attractive, yet powerful and conservative.

It needs to be easily printable. I would like the bleed removed in print so the black bar the bottom crosses the page (but the text is not near the edges)
Updates

Low design quality

Target Market(s)

Clients, Government Offices, Judiciary, Lawyers, Insurance Companies, Colleagues.

Industry/Entity Type

Law

Other font styles liked:
• Segoe UI LIght, Calibri Light,

Colors
00AB8E
00BBA5
67D7C9
C6EFE9
E9F9F6

Requirements
Must have
• Everything that is on the letterhead now.
Nice to have
• Cutting Edge design, yet conservative.
Should not have
• law firm cliche design, images,

```html
<!DOCTYPE html>
<html lang="en">
<head>
<meta charset="utf-8">
<title>Varenne Personal Injury Lawyers – Letterhead</title>
<link rel="stylesheet" href="https://fonts.googleapis.com/css2?family=Noto+Sans:wght@300;400&family=Roboto:wght@400;500&display=swap">
<style>
  :root {
    --green: #8ec900;
    --black: #1a1a1a;
    --ink: #2b2b2b;
    --muted: #6a6a6a;
    --paper: #f6f4f4;
    --white: #ffffff;
  }
  * { margin: 0; padding: 0; box-sizing: border-box; }
  html, body { width: 935px; height: 1200px; overflow: hidden; background: var(--paper); }
  .page {
    position: relative; width: 935px; height: 1200px; background: var(--paper);
    font-family: "Noto Sans", Arial, sans-serif; color: var(--ink); font-weight: 300;
  }
  .abs { position: absolute; }

  .brand-name {
    left: 44px; top: 52px; font-family: "Roboto", Arial, sans-serif; font-weight: 400;
    font-size: 62px; letter-spacing: 1px; line-height: 1; color: var(--black);
  }

  .contact-band { left: 615px; top: 34px; width: 320px; height: 112px; }
  .contact-list {
    right: 48px; top: 58px; list-style: none;
    font-family: "Roboto", Arial, sans-serif; font-size: 14px; color: var(--white); line-height: 20.5px;
  }
  .contact-item { display: flex; justify-content: flex-end; align-items: center; gap: 11px; height: 20.5px; }
  .contact-icon { width: 13px; height: 13px; flex: none; }

  .meta { font-size: 14.5px; line-height: 20px; }
  .meta-right { text-align: right; right: 60px; }
  .address { left: 48px; top: 235px; font-style: normal; }
  .re-label { left: 51px; top: 419px; }
  .re-body { left: 333px; top: 419px; }

  .divider { left: 61px; top: 514px; width: 756px; height: 1px; background: var(--ink); }

  .letter-body { left: 61px; top: 551px; width: 756px; font-size: 12px; line-height: 20.5px; text-align: justify; }
  .letter-body p + p { margin-top: 20px; }

  .closing { left: 62px; top: 854px; font-size: 13px; line-height: 17px; }
  .signature { left: 62px; top: 900px; width: 260px; height: 56px;
    background: linear-gradient(90deg, rgba(26,26,26,0.10), rgba(26,26,26,0.03)); }
  .signer { left: 67px; top: 976px; font-size: 13.5px; line-height: 17.5px; }

  .practice {
    left: 0; width: 935px; top: 1103px; text-align: center; font-size: 14px; line-height: 22px; color: var(--muted);
  }
  .practice strong { font-weight: 400; color: var(--ink); }

  .footer-bar {
    left: 0; top: 1167px; width: 935px; height: 33px; background: var(--black);
    color: var(--white); font-family: "Roboto", Arial, sans-serif; font-size: 14.5px;
    text-align: center; line-height: 33px;
  }
</style>
</head>
<body>
<div class="page">

  <div class="abs brand-name">VARENNE</div>

  <svg class="abs contact-band" viewBox="0 0 320 112" aria-hidden="true">
    <polygon points="0,0 320,0 320,112 42,112" fill="var(--green)"/>
    <polygon points="6,0 320,0 320,112 48,112" fill="var(--black)"/>
  </svg>
  <ul class="abs contact-list">
    <li class="contact-item"><span>905-555-0142</span>
      <svg class="contact-icon" viewBox="0 0 16 16" aria-hidden="true"><path d="M3 1c1-1 2-1 3 1l1 2c0 1-1 2-1 2 1 2 2 3 4 4 0 0 1-1 2-1l2 1c2 1 2 2 1 3-2 2-5 1-8-2S1 3 3 1z" fill="var(--green)"/></svg></li>
    <li class="contact-item"><span>905-555-0187</span>
      <svg class="contact-icon" viewBox="0 0 16 16" aria-hidden="true"><rect x="4" y="1" width="8" height="4" fill="var(--green)"/><rect x="1" y="5" width="14" height="7" rx="1" fill="var(--green)"/><rect x="4" y="11" width="8" height="4" fill="var(--green)"/></svg></li>
    <li class="contact-item"><span>Email: clara@corvelith.ca</span>
      <svg class="contact-icon" viewBox="0 0 16 16" aria-hidden="true"><rect x="1" y="3" width="14" height="10" fill="var(--green)"/><path d="M1 3l7 5 7-5" stroke="var(--black)" stroke-width="1.3" fill="none"/></svg></li>
    <li class="contact-item"><span>www.CORVELITH.ca</span>
      <svg class="contact-icon" viewBox="0 0 16 16" aria-hidden="true"><circle cx="8" cy="8" r="7" fill="var(--green)"/><path d="M4 5c2 1 2 3 4 3s1 3 3 5" stroke="var(--black)" stroke-width="1.3" fill="none"/></svg></li>
  </ul>

  <div class="abs meta" style="left:50px; top:166px;">Without Prejudice</div>
  <div class="abs meta" style="left:48px; top:199px;">By Email</div>
  <div class="abs meta meta-right" style="top:169px;">File Clerk: Clara Wexford</div>
  <div class="abs meta meta-right" style="top:206px; font-size:13.5px;">March 13, 2024</div>

  <address class="abs meta address">
    Norhaven Insurance Company<br>
    Claims Litigation Department<br>
    240 Aldergate Road South<br>
    P.O. Box 4100<br>
    Waterloo, ON &nbsp; N2J 0X7
  </address>
  <div class="abs meta" style="left:46px; top:354px;">Attention:&nbsp; Mr. Devon Marsh</div>
  <div class="abs meta" style="left:46px; top:382px;">Mr. Marsh:</div>

  <div class="abs meta re-label">Re:</div>
  <div class="abs meta re-body">
    Pellow v. Garnier et al.<br>
    DOL:&nbsp; September 12, 2019<br>
    Pre-Mediation Settlement Proposal – March 13th, 2024
  </div>

  <div class="abs divider"></div>

  <div class="abs letter-body">
    <p>Lorem ipsum dolor sit amet, consectetur adipiscing elit. Donec orci purus, luctus vitae dignissim eu, iaculis sed purus. Vivamus faucibus, ipsum nec aliquet viverra, leo mauris condimentum ligula, sit amet sagittis enim ligula quis arcu. Nam egestas tortor ivisi porttitor mattis. In tortor ante, ultricies in suscipit a, tempus non massa. Vivamus et auctor mi. Fusce vel massa nulla. Phasellus nec eros mauris, et scelerisque orci.</p>
    <p>Donec malesuada orci vitae nulla accumsan porta a id massa. Quisque accumsan iaculis magna sit amet fringilla. Maecenas consequat, magna eget tincidunt semper, odio nibh rutrum mi, id feugiat ante nisi eu risus. Vestibulum nunc orci, rhoncus a placerat in, ultricies in mi. Cras mattis varius eros, vel fringilla nisi suscipit eget. Quisque scelerisque sagittis nulla at porttitor.</p>
    <p>Sed id augue vitae urna euismod commodo aliquet a quam. Pellentesque arcu velit, cursus et malesuada ut, consequat et diam. Nullam erat sem, rhoncus id ullamcorper vitae, rhoncus et arcu. In ultricies ultricies nulla, ut rutrum nisi iaculis at. Donec eu magna a metus ornare faucibus. Fusce aliquet faucibus ultricies. Morbi semper, est id tincidunt gravida, sem arcu adipiscing</p>
  </div>

  <div class="abs closing">Yours very truly,<br>VARENNE PERSONAL INJURY LAWYERS</div>
  <div class="abs signature" role="img" aria-label="Handwritten signature of Owen T. Varenne"></div>
  <div class="abs signer">
    Owen T. Varenne<br>
    Varenne Law Professional Corporation<br>
    /cw<br>
    Encl.
  </div>

  <div class="abs practice">
    <strong>Practice Restricted-</strong> Serious Personal Injury, Wrongful Death Litigation<br>
    Long-Term Disability Litigation, Wrongful Dismissal Litigation, Employee Terminations
  </div>

  <div class="abs footer-bar">48 Harbour Street E., Suite 920, Hamilton, ON&nbsp; L8P 2K6</div>
</div>
</body>
</html>
```